Client Fund Fact Sheet Flyer - Investment Advisory

We require this 3 page flyer document polished and made to look professional by a designer. There may be repeat work for the . The logo is provided in the uploaded files and the colour codes and fonts to be used are: Colour - Orange
PMS 144
RGB (222, 135, 3)
#de8703

Colour - Grey
PMS 432
RGB (51,51,51)
#333333

Fonts
Family: Helvetica Neue
Cuts: 57 Condensed
67 Medium Condensed

Target Market(s)

Clients of an investment management firm

Industry/Entity Type

Investment Advisory

Font styles to use
Other font styles liked:
• Helvetica Neue

Requirements
Must have
• Tables and charts, look professional
Should not have
• Should not look like it was made in word or publisher by us!

```html
<!DOCTYPE html>
<html lang="en">
<head>
<meta charset="utf-8">
<title>Balanced Growth – Investment Beliefs</title>
<link rel="stylesheet" href="https://fonts.googleapis.com/css2?family=Oswald:wght@500&family=Lato:wght@400;700&family=Arimo:wght@400;700&display=swap">
<style>
  :root {
    --orange: #de8703;
    --orange-bright: #ef7f0a;
    --cream: #fdf4e6;
    --peach: #fbe5cd;
    --grey: #333333;
    --text-grey: #555555;
    --footer-dark: #3d4550;
    --white: #ffffff;
  }
  * { box-sizing: border-box; margin: 0; padding: 0; }
  html, body { width: 848px; height: 1200px; overflow: hidden; background: var(--white); }
  .page { position: relative; width: 848px; height: 1200px; overflow: hidden; font-family: "Lato", sans-serif; color: var(--grey); }
  .page-bg { position: absolute; inset: 0; }

  .issue-date { position: absolute; left: 65px; top: 22px; font: 700 14px "Arimo", sans-serif; color: #111; }
  .fund-title { position: absolute; left: 60px; top: 48px; font: 500 70px/1 "Oswald", sans-serif; color: var(--orange); letter-spacing: -1px; transform: scaleX(0.9); transform-origin: left; }
  .brand { position: absolute; right: 48px; top: 30px; text-align: right; font: 700 22px/1.05 "Lato", sans-serif; color: var(--orange-bright); }
  .brand .sq { display: inline-block; width: 10px; height: 10px; background: var(--orange-bright); margin-right: 6px; vertical-align: 3px; }
  .section-title { position: absolute; left: 63px; top: 136px; font: 700 20px "Arimo", sans-serif; color: #111; }

  .approach { position: absolute; left: 57px; top: 178px; width: 740px; height: 198px; border: 1.5px solid var(--orange-bright); }
  .approach-head { margin-top: 16px; height: 25px; background: var(--orange-bright); color: var(--white); text-align: center; font: 400 15px/25px "Lato", sans-serif; letter-spacing: .3px; }
  .approach-body { padding: 14px 24px 0 24px; font-size: 12.8px; line-height: 18px; color: var(--text-grey); }
  .approach-body p + p { margin-top: 18px; }

  .beliefs { position: absolute; left: 52px; top: 418px; width: 740px; display: grid; grid-template-columns: 131px 131px 243px 235px; }
  .beliefs .hd { background: var(--orange); color: var(--grey); font: 700 10.5px "Lato", sans-serif; display: flex; align-items: center; justify-content: center; height: 35px; margin-bottom: 1.5px; }
  .beliefs .hd.belief { margin-right: 1.5px; }
  .beliefs .blank { height: 35px; }
  .row { display: contents; }
  .cell { display: flex; align-items: center; font-size: 10px; line-height: 14px; letter-spacing: .2px; border-bottom: 1px dotted #e5d3bd; }
  .row.tint .cell { background: var(--peach); }
  .row.tint .cell + .cell { border-left: 1.5px solid var(--white); }
  .cell.icon { justify-content: center; }
  .cell.name { justify-content: center; text-align: center; font-weight: 700; padding: 0 12px; }
  .cell.text { padding: 0 12px 0 13px; text-align: justify; }
  .icon svg { fill: var(--orange); }
  .dollar { font: 700 54px "Arimo", sans-serif; color: var(--orange); }

  .footer { position: absolute; left: 0; top: 1122px; width: 848px; height: 78px; display: flex; }
  .footer-brand { width: 143px; background: var(--footer-dark); color: var(--white); font: 700 13px/1.1 "Lato", sans-serif; display: flex; align-items: center; justify-content: center; text-align: center; margin-right: 2px; }
  .footer-note { flex: 1; background: var(--orange-bright); color: var(--white); font: 400 10px/15px "Arimo", sans-serif; padding: 16px 40px 0 9px; }
</style>
</head>
<body>
<div class="page">
  <svg class="page-bg" width="848" height="1200" aria-hidden="true">
    <rect x="0" y="0" width="848" height="124" fill="#fdf4e6"/>
    <polygon points="510,124 582,0 630,0 732,176 848,176 848,124" fill="#fdf4e6"/>
    <polygon points="582,0 630,0 732,176 510,124" fill="#ffffff"/>
    <polygon points="798,290 848,290 848,380" fill="#fdf4e6"/>
  </svg>

  <div class="issue-date">19 March 2021</div>
  <h1 class="fund-title">BALANCED GROWTH</h1>
  <div class="brand"><span class="sq"></span>Meridian<br>Financial Group</div>
  <h2 class="section-title">Investment Beliefs</h2>

  <section class="approach">
    <div class="approach-head">OUR APPROACH</div>
    <div class="approach-body">
      <p>Our investment approach aims to deliver strong long-term investment returns, over and above inflation, to help you build your wealth.</p>
      <p>We carefully consider investments and expose our clients to risk only when we believe will be adequately rewarded.</p>
      <p>We take an objective approach to investment selection and have no bias towards any type of investment.</p>
    </div>
  </section>

  <section class="beliefs">
    <div class="blank"></div><div class="blank"></div>
    <div class="hd belief">Belief</div><div class="hd">Principle</div>

    <div class="row tint" style="grid-row:2">
      <div class="cell icon" style="height:152px"><span class="dollar">$</span></div>
      <div class="cell name">1. Economic or Exceptional</div>
      <div class="cell text">Above market returns can be achieved by active managers who possess skill and experience. It is challenging however to reliably identify skillful managers in advance.</div>
      <div class="cell text">A high bar will be set for the inclusion of active management and we will seek to access the best ideas from external fund managers. The default allocation will be through an index and fees paid where there is high conviction of excess return potential or diversification benefits.</div>
    </div>

    <div class="row">
      <div class="cell icon" style="height:97px">
        <svg width="42" height="42" viewBox="0 0 42 42"><path d="M21 21 V0 A21 21 0 1 0 35.8 35.8 Z"/><path d="M23.5 1 A20 20 0 0 1 41 18.5 H23.5 Z"/><path d="M24 21.5 H41 A20 20 0 0 1 36 34.5 Z"/></svg>
      </div>
      <div class="cell name">2. Diversify<br>where it counts</div>
      <div class="cell text">Genuine portfolio diversification is the primary tool available to manage risk.</div>
      <div class="cell text">Diversification should be achieved by investing across different asset classes, and within asset classes by accessing a range of managers and strategies.</div>
    </div>

    <div class="row tint">
      <div class="cell icon" style="height:69px">
        <svg width="40" height="38" viewBox="0 0 40 38"><rect x="28" y="2" width="10" height="4" transform="rotate(-20 33 4)"/><rect x="0" y="10" width="12" height="5"/><rect x="14" y="10" width="12" height="5"/><rect x="0" y="18" width="6" height="5"/><rect x="8" y="18" width="12" height="5"/><rect x="22" y="18" width="12" height="5"/><rect x="0" y="26" width="12" height="5"/><rect x="14" y="26" width="12" height="5"/><rect x="28" y="26" width="10" height="5"/><rect x="0" y="33" width="6" height="5"/><rect x="8" y="33" width="12" height="5"/><rect x="22" y="33" width="16" height="5"/></svg>
      </div>
      <div class="cell name">3.Client Centric Risk Setting</div>
      <div class="cell text" style="text-align:left">Risk for Meridian's clients is primarily the risk of permanent capital loss.</div>
      <div class="cell text">Risk will be defined and measured as the magnitude of a severe loss in portfolio construction.</div>
    </div>

    <div class="row">
      <div class="cell icon" style="height:76px">
        <svg width="40" height="42" viewBox="0 0 40 42"><path d="M8 0 H32 V12 A12 12 0 0 1 24 23.5 V30 H30 V36 H10 V30 H16 V23.5 A12 12 0 0 1 8 12 Z"/><path d="M8 3 H2 V8 A10 10 0 0 0 9 17.5 L10 14 A6 6 0 0 1 5 8 V6 H8 Z M32 3 H38 V8 A10 10 0 0 1 31 17.5 L30 14 A6 6 0 0 0 35 8 V6 H32 Z"/><rect x="7" y="38" width="26" height="4"/></svg>
      </div>
      <div class="cell name">4. A competitive offering</div>
      <div class="cell text">Our clients expect to achieve strong investment results from investing with us compared to other options.</div>
      <div class="cell text">Portfolios will be benchmarked against publicly available surveys of competing offerings.</div>
    </div>

    <div class="row tint">
      <div class="cell icon" style="height:91px">
        <div role="img" aria-label="Handshake icon" style="width:46px;height:28px;background:var(--orange);border-radius:6px"></div>
      </div>
      <div class="cell name">5.Partner with Professionals</div>
      <div class="cell text">Listening to external expertise will lead to stronger investment outcomes for our clients.</div>
      <div class="cell text">We will engage professional portfolio construction and asset management expertise to both select agents and invest in securities for our clients.</div>
    </div>

    <div class="row">
      <div class="cell icon" style="height:58px">
        <svg width="50" height="36" viewBox="0 0 50 36"><polyline points="3,17 18,31 47,3" fill="none" stroke="#de8703" stroke-width="6"/></svg>
      </div>
      <div class="cell name">6.Keep it Simple</div>
      <div class="cell text">Good ideas get lost in complexity. Our clients deserve to understand where their savings are invested.</div>
      <div class="cell text">Portfolios will be only as complicated as required to achieve risk and return objectives.</div>
    </div>

    <div class="row tint">
      <div class="cell icon" style="height:91px">
        <div role="img" aria-label="Chess pieces icon" style="width:40px;height:36px;background:var(--orange);border-radius:4px"></div>
      </div>
      <div class="cell name">7.Be Patient</div>
      <div class="cell text">Markets are not always efficiently priced, but it is challenging to identify opportunities to take advantage of mispricing.</div>
      <div class="cell text">We will set diversified strategic asset allocations that reflect the risk appetites and time horizons of our clients. Active decisions will be focused on managing risk to our clients.</div>
    </div>
  </section>

  <footer class="footer">
    <div class="footer-brand">Meridian<br>Financial Group</div>
    <div class="footer-note">This document relates to the Meridian Financial Group Managed Models for which Northvale has appointed Keystone Capital Pty Ltd (ABN 12 345 678 901) (<b>‘Keystone Capital’</b>), an Authorised representative of AFS Licence No. 000000 as the Model Manager.</div>
  </footer>
</div>
</body>
</html>
```